Classy, Elegant, Simple Business Card Design

Looking to have a classy, simple, and elegant design. Want a top notch designed business card. I really like the look of the new torvane credit card. I also like the design I attached. I am trying to reach 21-29 year old females for booking us for there wedding or event. We offer Disc Jockey Service, Photo Booth Rentals, and Uplighting .

Target Market(s)

21-28 year old females

Contact Information for Business Card

Has to have logo, website, email, and phone number

Font styles to use
Other font styles liked:
• open to font choice, modern, clean
Designer to choose
33a6d7
0791cd
0555a3
ffffff

Requirements
Must have
• Has to have logo, website, email, and phone number
Nice to have
• I really like the design of the new torvane credit card. I also included my logo and some designs I like
Should not have
• clutter or too much info

```html
<!DOCTYPE html>
<html lang="en">
<head>
<meta charset="utf-8">
<title>Tidemark Event Group — Business Card</title>
<link href="https://fonts.googleapis.com/css2?family=Questrial&family=Roboto:wght@400;700&display=swap" rel="stylesheet">
<style>
  :root {
    --sky: #33a6d7;
    --azure: #0791cd;
    --deep: #0555a3;
    --white: #ffffff;
    --card: #1f2023;
    --stage: #3b3c3e;
    --muted: #8a8d92;
  }
  * { box-sizing: border-box; margin: 0; padding: 0; }
  html, body { width: 799px; height: 1200px; overflow: hidden; }
  body {
    background: var(--stage);
    font-family: "Roboto", sans-serif;
    position: relative;
  }
  .card {
    position: absolute;
    left: 80px;
    width: 640px;
    height: 366px;
    background: var(--card);
    border-radius: 4px;
    box-shadow: 0 14px 30px rgba(0,0,0,0.45);
    overflow: hidden;
  }
  .card--front { top: 150px; }
  .card--back { top: 690px; }

  .brand {
    position: absolute;
    display: flex;
    align-items: center;
    gap: 12px;
    font-family: "Questrial", sans-serif;
    color: var(--azure);
    letter-spacing: 3px;
  }
  .brand__dot {
    width: 14px; height: 14px;
    border-radius: 50%;
    background: var(--azure);
    flex: none;
  }
  .brand__name { font-size: 30px; line-height: 1.1; }
  .brand__name small { display: block; font-size: 15px; letter-spacing: 6px; }

  .card--front .brand { left: 50%; top: 110px; transform: translateX(-50%); }

  .equalizer {
    position: absolute;
    left: 0; bottom: 0;
    width: 640px; height: 130px;
  }

  .card--back .brand { right: 44px; top: 78px; }
  .brand--back .brand__name { font-size: 26px; }
  .brand--back .brand__name small { font-size: 13px; }

  .person { position: absolute; left: 40px; top: 150px; }
  .person__name { color: var(--azure); font-weight: 700; font-size: 22px; }
  .person__role { color: var(--white); font-size: 14px; margin-top: 2px; }

  .contact {
    position: absolute;
    display: flex;
    align-items: center;
    gap: 8px;
    color: var(--white);
    font-size: 15px;
  }
  .contact svg { width: 14px; height: 14px; fill: var(--azure); flex: none; }
  .contact--phone { left: 40px; top: 232px; }
  .contact--email { left: 40px; top: 300px; }
  .contact--web { left: 330px; top: 300px; }

  .divider {
    position: absolute;
    left: 40px; right: 40px; top: 275px;
    height: 2px;
    background: var(--azure);
  }
</style>
</head>
<body>

<section class="card card--front">
  <div class="brand">
    <span class="brand__dot"></span>
    <span class="brand__name">TIDEMARK<small>EVENT GROUP</small></span>
  </div>
  <svg class="equalizer" viewBox="0 0 640 130" role="img" aria-label="Blue equalizer bar pattern along the lower edge">
    <defs>
      <linearGradient id="eqFill" x1="0" y1="0" x2="1" y2="0">
        <stop offset="0" stop-color="#33a6d7"/>
        <stop offset="1" stop-color="#0555a3"/>
      </linearGradient>
    </defs>
    <polygon points="0,20 640,70 640,130 0,130" fill="url(#eqFill)" opacity="0.85"/>
  </svg>
</section>

<section class="card card--back">
  <div class="brand brand--back">
    <span class="brand__dot"></span>
    <span class="brand__name">TIDEMARK<small>EVENT GROUP</small></span>
  </div>

  <div class="person">
    <p class="person__name">Nora Vale</p>
    <p class="person__role">Founder &amp; CEO</p>
  </div>

  <p class="contact contact--phone">
    <svg viewBox="0 0 24 24" aria-hidden="true"><path d="M6.6 10.8a15.1 15.1 0 0 0 6.6 6.6l2.2-2.2a1 1 0 0 1 1-.25 11.4 11.4 0 0 0 3.6.6 1 1 0 0 1 1 1V20a1 1 0 0 1-1 1A17 17 0 0 1 3 4a1 1 0 0 1 1-1h3.5a1 1 0 0 1 1 1c0 1.25.2 2.45.6 3.6a1 1 0 0 1-.25 1z"/></svg>
    555 0147 0198
  </p>

  <div class="divider"></div>

  <p class="contact contact--email">
    <svg viewBox="0 0 24 24" aria-hidden="true"><path d="M2 5h20v14H2zm2 2v.5l8 5 8-5V7l-8 5z"/></svg>
    nora@tidemarkevents.com
  </p>

  <p class="contact contact--web">
    <svg viewBox="0 0 24 24" aria-hidden="true"><circle cx="12" cy="12" r="10"/></svg>
    www.tidemarkevents.com
  </p>
</section>

</body>
</html>
```